Business card design for modern PanoWalk agency

Hello,

I need a business card design for my company Kites7Market.
We mainly offer Zorvex PanoWalk Tours (360° Photography) and it should be a business card with following details:

Name: Tobias Wendler
Number: +49 176 58 20 917
Mail: tobias@kites7market.com
website: kites7market.com

Main colour that we use is the red of the logo.
It´s also important to integrate the "Zorvex Verified logo" as the person on this business card is a Zorvex verified photographer.

And if possible we would also like to integrate something like send us a sms or chatterly and we call you back. As the number is german but we sell now in Vienna, Austria.

We offer a good price but very high photography quality, as we are mostly students - that´s our concept.

Maybe an idea is to integrate something 360° on the back-side of the card, for example the photo attached (just an idea) or some great design.
See flyer (attached) and kites7market.com for inspiration, maybe use of the photo of me (attached) in a circle or something

I´m very excited for your designs and thanks a lot in advance!! :)

Target Market(s)

Shops, hotels, shopping centers, etc. in Vienna, Austria

Industry/Entity Type

Business

Contact Information for Business Card

double-sided, use red of the logo, 360° zorvex pano walk certified photographer

Font styles to use
Serif
Sans Serif

Colors
ec1f27

Requirements
Nice to have
• maybe some 360° design on back-side
• maybe include photo of me in a circle or something or sketched in red colour

```html
<!DOCTYPE html>
<html lang="en">
<head>
<meta charset="utf-8">
<title>Kites7Market – Business Card</title>
<link rel="stylesheet" href="https://fonts.googleapis.com/css2?family=Open+Sans:wght@400;600;700&display=swap">
<style>
  :root {
    --bg: #3a3532;
    --card: #0d0d0d;
    --card-edge: #1a1a1a;
    --brand-red: #ec1f27;
    --text-light: #e6e6e6;
    --text-grey: #b5b5b5;
    --divider: #2e2e2e;
    --verified-green: #1faa4b;
  }
  * { box-sizing: border-box; margin: 0; padding: 0; }
  html, body {
    width: 1200px;
    height: 900px;
    overflow: hidden;
    background: var(--bg);
    font-family: "Open Sans", Arial, sans-serif;
  }
  .canvas {
    width: 1200px;
    height: 900px;
    display: flex;
    align-items: center;
    justify-content: center;
    gap: 40px;
  }
  .card {
    width: 540px;
    height: 310px;
    background: var(--card);
    border: 1px solid var(--card-edge);
    border-radius: 4px;
    position: relative;
    box-shadow: 0 10px 30px rgba(0,0,0,.45);
  }

  /* Front */
  .brand {
    position: absolute;
    left: 40px;
    top: 112px;
    width: 196px;
    display: flex;
    align-items: center;
    gap: 10px;
  }
  .brand-square {
    width: 46px;
    height: 46px;
    flex: none;
    background: var(--brand-red);
  }
  .brand-name {
    font-weight: 700;
    font-size: 21px;
    line-height: 21px;
    color: var(--text-grey);
    letter-spacing: .5px;
  }
  .brand-line { display: block; }
  .divider {
    position: absolute;
    left: 250px;
    top: 58px;
    width: 1px;
    height: 110px;
    background: var(--divider);
  }
  .contact {
    position: absolute;
    left: 272px;
    top: 62px;
  }
  .contact-name {
    color: var(--brand-red);
    font-weight: 600;
    font-size: 17px;
    margin-bottom: 6px;
  }
  .contact-list { list-style: none; }
  .contact-item {
    display: flex;
    align-items: center;
    gap: 10px;
    color: var(--text-light);
    font-size: 14px;
    line-height: 22px;
    white-space: nowrap;
  }
  .contact-icon { width: 11px; height: 11px; flex: none; }
  .callback-note {
    position: absolute;
    left: 0;
    right: 0;
    bottom: 54px;
    text-align: center;
    color: var(--text-light);
    font-size: 15px;
  }

  /* Back */
  .photo {
    position: absolute;
    top: 70px;
    width: 200px;
    height: 130px;
    border-radius: 8px;
  }
  .photo-runner {
    left: 60px;
    background: linear-gradient(160deg, #d9c9a3 0%, #a88a5c 45%, #5b4a3a 100%);
  }
  .photo-skater {
    left: 280px;
    background: linear-gradient(90deg, #c9ddd3 0%, #e8ead8 55%, #f0a060 100%);
  }
  .verified-badge {
    position: absolute;
    left: 205px;
    top: 218px;
    width: 130px;
    height: 26px;
    border-radius: 13px;
    background: var(--verified-green);
  }
</style>
</head>
<body>
<main class="canvas">

  <section class="card card-front" aria-label="Card front">
    <div class="brand">
      <span class="brand-square"></span>
      <span class="brand-name"><span class="brand-line">KITES7</span><span class="brand-line">MARKET</span></span>
    </div>

    <div class="divider"></div>

    <div class="contact">
      <p class="contact-name">Tobias Wendler</p>
      <ul class="contact-list">
        <li class="contact-item">
          <svg class="contact-icon" viewBox="0 0 12 12"><rect x="3" y="0.5" width="6" height="11" rx="1" fill="none" stroke="#ec1f27" stroke-width="1.3"/><circle cx="6" cy="9.5" r=".8" fill="#ec1f27"/></svg>
          +49 176 58 20 917
        </li>
        <li class="contact-item">
          <svg class="contact-icon" viewBox="0 0 12 12"><rect x="0.5" y="2" width="11" height="8" fill="#ec1f27"/><path d="M0.5 2 L6 6.5 L11.5 2" fill="none" stroke="#0d0d0d" stroke-width="1"/></svg>
          tobias@kites7market.com
        </li>
        <li class="contact-item">
          <svg class="contact-icon" viewBox="0 0 12 12"><circle cx="6" cy="6" r="5.5" fill="#ec1f27"/><path d="M1 6 H11 M6 .5 C3 3 3 9 6 11.5 M6 .5 C9 3 9 9 6 11.5" fill="none" stroke="#0d0d0d" stroke-width=".8"/></svg>
          kites7market.com
        </li>
      </ul>
    </div>

    <p class="callback-note">Send us a sms or chatterly and we call you back</p>
  </section>

  <section class="card card-back" aria-label="Card back">
    <div class="photo photo-runner" role="img" aria-label="Photo of running shoes stepping on a road"></div>
    <div class="photo photo-skater" role="img" aria-label="Photo of a skateboarder silhouetted on a bridge at sunset"></div>
    <div class="verified-badge" role="img" aria-label="Zorvex verified badge"></div>
  </section>

</main>
</body>
</html>
```